Sell the dream! Property investment proposal document

We are looking for a proposal document which outlines our vision for property development. The purpose of the document is to raise investment from investors - sell the dream!
Brief summary:
Kestrel Dwellings Developments, is an emerging New Zealand property investment company with a focus on providing unique property investment opportunities.
Our expertise and capabilities in architectural modular homes provide us with a remarkable advantage in tackling the development of properties that are typically considered challenging, remote, or uniquely positioned.
Our specialization in this niche sector of property development not only sets us apart from competitors, but also paves the way for lucrative investment opportunities in the New Zealand property market.
Feel free to use any images from www.kestreldwellings.co.nz
Target Market(s)
investors for a unique property development opportunity
Industry/Entity Type
luxury property development in unique locations throughout New Zealand
Colors
Designer to choose only greyscale colors for use in the design.
Look and feel

```html
<!DOCTYPE html>
<html lang="en">
<head>
<meta charset="utf-8">
<title>Kestrel Dwellings – Investment Proposal</title>
<link rel="stylesheet" href="https://fonts.googleapis.com/css2?family=Questrial&display=swap">
<style>
  :root {
    --board: #8f8f92;
    --board-dark: #5c5c5f;
    --page: #1c1b1d;
    --band: #3a393c;
    --band-soft: #2b2a2d;
    --ink: #ffffff;
    --ink-soft: #bdbdbd;
    --label: #111111;
  }
  * { box-sizing: border-box; margin: 0; padding: 0; }
  html, body { width: 1037px; height: 1200px; overflow: hidden; }
  body {
    position: relative;
    background: linear-gradient(135deg, var(--board-dark) 0%, var(--board) 35%, var(--board) 65%, var(--board-dark) 100%);
    font-family: "Questrial", "Century Gothic", sans-serif;
    color: var(--ink);
  }
  .page-label {
    position: absolute; width: 472px; text-align: center;
    font-size: 14px; color: var(--label);
  }
  .page {
    position: absolute; width: 472px; height: 334px;
    background: var(--page); overflow: hidden;
    box-shadow: 0 14px 14px rgba(0,0,0,0.35);
  }
  .photo { position: absolute; }
  .band { position: absolute; background: var(--band); }
  .band-soft { position: absolute; background: var(--band-soft); }
  .wordmark { position: absolute; line-height: 1; letter-spacing: -1px; color: var(--ink); }
  .brand-tag {
    position: absolute; display: flex; align-items: center; gap: 6px;
    font-size: 10px; color: var(--ink); white-space: nowrap;
  }
  .brand-tag::before { content: ""; width: 7px; height: 7px; background: var(--ink); }
  .heading-box {
    position: absolute; background: var(--band);
    font-size: 15px; padding: 4px 0 0 12px; height: 26px; white-space: nowrap;
  }
  .body-copy { position: absolute; font-size: 5px; line-height: 10px; color: var(--ink-soft); text-align: justify; }
  .body-copy p + p { margin-top: 10px; }
  .side-title {
    position: absolute; writing-mode: vertical-rl; transform: rotate(180deg);
    font-size: 14px; white-space: nowrap; display: flex; align-items: center; justify-content: center;
  }
</style>
</head>
<body>

<!-- Back cover -->
<div class="page-label" style="left:41px; top:19px;">Back</div>
<section class="page" style="left:41px; top:46px;">
  <div class="band" style="left:111px; top:0; width:23px; height:64px;"></div>
  <div class="band" style="left:329px; top:0; width:23px; height:64px;"></div>
  <div class="wordmark" style="left:134px; top:6px; width:195px; text-align:center; font-size:44px;">Kestrel</div>
  <div class="photo" role="img" aria-label="Black and white photo of a dark timber modular home with a white deck among trees and lawn"
       style="left:30px; top:64px; width:413px; height:206px; background:linear-gradient(180deg,#d9d9d9 0%,#a8a8a8 45%,#3a3a3a 62%,#8a8a8a 80%,#b5b5b5 100%);"></div>
  <div style="position:absolute; left:30px; top:300px; font-size:9px; line-height:15px; color:var(--ink-soft);">
    <div style="padding-left:28px;">Ph: 09 555 0142</div>
    <div>Web: www.kestreldwellings.co.nz</div>
  </div>
  <div class="brand-tag" style="left:328px; top:307px;">Kestrel Dwellings</div>
</section>

<!-- Front cover -->
<div class="page-label" style="left:523px; top:19px;">Front</div>
<section class="page" style="left:523px; top:46px;">
  <div style="position:absolute; left:0; top:0; width:472px; height:36px; text-align:center; font-size:21px; letter-spacing:4px; padding-top:7px;">Sell the dream!</div>
  <div class="photo" role="img" aria-label="Photo of a dark timber U-shaped modular home with glass walls, a lit courtyard and blurred trees behind"
       style="left:0; top:36px; width:472px; height:244px; background:linear-gradient(180deg,#cfcfcf 0%,#9a9a9a 35%,#2e2b28 55%,#7a6e62 75%,#4a4a4a 100%);"></div>
  <div class="band" style="left:311px; top:280px; width:13px; height:54px;"></div>
  <div class="band" style="left:447px; top:280px; width:9px; height:54px;"></div>
  <div class="wordmark" style="left:26px; top:228px; font-size:88px;">Kestrel</div>
  <div class="brand-tag" style="left:340px; top:300px;">Kestrel Dwellings</div>
</section>

<!-- Page 2 -->
<div class="page-label" style="left:41px; top:401px;">Page 2</div>
<section class="page" style="left:41px; top:424px;">
  <div class="photo" role="img" aria-label="Photo of a modern bedroom with a dark upholstered bed, slatted timber headboard wall and line art prints"
       style="left:0; top:0; width:247px; height:334px; background:linear-gradient(180deg,#e6e4e1 0%,#cfcbc6 45%,#5c5c5c 70%,#b9b9b9 85%,#6e5a4a 100%);"></div>
  <div style="position:absolute; left:70px; top:300px; font-size:36px; color:rgba(255,255,255,0.25); line-height:1;">Kestrel</div>
  <div class="heading-box" style="left:247px; top:9px; width:184px;">Business Origins</div>
  <div class="body-copy" style="left:261px; top:42px; width:197px;">
    <p>Kestrel Dwellings Developments was established with the goal of transforming the property investment market in New Zealand by introducing an innovative approach that centers on architectural modular designs and streamlined project timelines.</p>
    <p>Driven by our enthusiasm for architecture and real estate, we have expanded our successful business model to not only offer financial opportunities for investors but also to expand on our passion for high-end architectural design.</p>
    <p>With a wealth of experience accumulated over the past six years in the construction and the property market, we are pivoting to focus solely on our property development initiatives, presenting completed Kestrel projects to the market, in exclusive locations.</p>
    <p>These projects will boast high-quality standards, meticulous attention to detail and landscaping, and creative design elements.</p>
    <p>By introducing completed Kestrel properties into the market, we aim to reach a wider audience, catering to individuals who prefer ready-to-occupy homes, over engaging in the design and construction process. This approach also simplifies the financing process for prospective buyers, as established properties are often preferred by financial lenders.</p>
  </div>
  <div class="brand-tag" style="left:290px; top:305px; font-size:12px;">Kestrel Dwellings</div>
</section>

<!-- Page 1 -->
<div class="page-label" style="left:523px; top:401px;">Page 1</div>
<section class="page" style="left:523px; top:424px;">
  <div class="photo" role="img" aria-label="Photo of a bright open-plan living room with a white sectional sofa, dining table and tall windows to the garden"
       style="left:0; top:16px; width:472px; height:141px; background:linear-gradient(180deg,#f1efec 0%,#dedad5 50%,#8a8580 75%,#4a4440 100%);"></div>
  <div class="band" style="left:40px; top:157px; width:28px; height:177px;"></div>
  <div class="side-title" style="left:40px; top:157px; width:28px; height:177px;">Business Overview</div>
  <div class="band-soft" style="left:203px; top:157px; width:19px; height:177px;"></div>
  <div class="band" style="left:383px; top:157px; width:20px; height:177px;"></div>
  <div class="body-copy" style="left:80px; top:176px; width:130px;">
    Kestrel Dwellings Developments, is an emerging New Zealand property investment company with a focus on providing unique property investment opportunities.<br>
    Our expertise and capabilities in architectural modular homes provide us with a remarkable advantage in tackling the development of properties that are typically considered challenging, remote, or uniquely positioned.<br>
    As a company, with 48 employees boasting a wealth of experience in handling complex architectural projects, making us well-equipped to navigate the intricacies and demands of such ventures.
  </div>
  <div class="body-copy" style="left:229px; top:176px; width:130px;">
    This advantage allows us to not only execute projects efficiently but also to deliver exceptional results within condensed time frames.<br>
    By capitalizing on our ability to develop difficult, remote, or one-of-a-kind properties swiftly and effectively, Kestrel Dwellings Developments offers investors a rare chance to engage in projects that promise exceptional profitability in the New Zealand property market.<br>
    Our specialization in this niche sector of property development not only sets us apart from competitors, but also paves the way for lucrative investment opportunities in the New Zealand property market.
  </div>
  <div class="side-title" style="left:410px; top:165px; width:55px; height:160px; font-size:12px;">Kestrel Dwellings</div>
</section>

<!-- Page 4 -->
<div class="page-label" style="left:41px; top:778px;">Page 4</div>
<section class="page" style="left:41px; top:801px;">
  <div class="band" style="left:0; top:0; width:37px; height:334px;"></div>
  <div class="side-title" style="left:0; top:0; width:37px; height:190px; font-size:15px;">Financial Summary</div>
  <div class="band-soft" style="left:176px; top:0; width:31px; height:57px;"></div>
  <div class="wordmark" style="left:207px; top:4px; width:265px; text-align:center; font-size:46px;">Kestrel</div>
  <div class="body-copy" style="left:44px; top:14px; width:117px; line-height:11.3px;">
    <p>In terms of financial projections, with each development, we anticipate a profit of 10%-20% which will be project dependent.</p>
    <p style="margin-top:5px;">This growth is fueled by the increasing demand for unique property investments in New Zealand and our ability to deliver high-quality services to the market in a condensed time frame, with heavily controlled costs.</p>
    <p style="margin-top:5px;">With a solid business model and a dedicated team, we are confident in our ability to achieve success and establish Kestrel Dwellings Investments as a trusted name in the industry.</p>
    <p style="margin-top:5px;">New Zealand's property market has been experiencing steady growth over the years, making it an attractive destination for property investors. With its beautiful landscapes and strong economy, New Zealand offers a diverse range of investment opportunities for both local and international investors. The demand for quality properties in prime locations continues to rise, creating a favorable environment for property investment companies like ours that can lean on our modular benefits of being able to reach unique and remote locations.</p>
  </div>
  <div class="photo" role="img" aria-label="Photo of a long pale living space with white sofas, sheer curtains and a timber kitchen at the far end"
       style="left:169px; top:57px; width:303px; height:217px; background:linear-gradient(180deg,#c9c4c4 0%,#e7e3e0 40%,#bdb6ae 70%,#8c8580 100%);"></div>
  <div class="brand-tag" style="left:255px; top:306px;">Kestrel Dwellings</div>
</section>

<!-- Page 3 -->
<div class="page-label" style="left:523px; top:778px;">Page 3</div>
<section class="page" style="left:523px; top:801px;">
  <div class="heading-box" style="left:0; top:12px; width:204px;">Competitive Advantage</div>
  <div class="body-copy" style="left:14px; top:43px; width:241px;">
    <p>Our competitive advantage lies in the uniqueness of our property investment opportunities. Unlike traditional real estate companies, we focus on offering properties that are not only profitable but also aesthetically pleasing and unique. By catering to the tastes of architecture lovers, we set ourselves apart from the competition and attract a niche market of customers who appreciate the artistry and design of our projects.</p>
    <p>Additionally, the streamlined and condensed timelines facilitated by our modular approach provide quicker returns on investment.</p>
  </div>
  <div class="brand-tag" style="left:135px; top:140px;">Kestrel Dwellings</div>
  <div class="photo" role="img" aria-label="Photo of a glass-walled room looking out over green hills and a coastal bay"
       style="left:266px; top:0; width:206px; height:173px; background:linear-gradient(180deg,#e9eef0 0%,#a9b4bb 35%,#7c8a5e 60%,#4d4a45 85%,#2c2a29 100%);"></div>
  <div class="photo" role="img" aria-label="Photo of a dark timber lounge with white sofas and tall plants opening to a deck"
       style="left:0; top:173px; width:288px; height:161px; background:linear-gradient(180deg,#d8d6d3 0%,#6f6c69 45%,#3c3b3c 75%,#6a6a6a 100%);"></div>
  <div style="position:absolute; left:250px; top:190px; writing-mode:vertical-rl; transform:rotate(180deg); font-size:40px; color:rgba(255,255,255,0.3); line-height:1;">Kestrel</div>
  <div class="photo" role="img" aria-label="Photo of lounge chairs by a window overlooking the ocean and a grassy headland"
       style="left:288px; top:173px; width:184px; height:161px; background:linear-gradient(180deg,#eef2f5 0%,#a6bccb 35%,#2f5c7a 60%,#2a4a60 80%,#1d1d1d 100%);"></div>
</section>

</body>
</html>
```